New Business Card Design Project

I need a design for business cards, i am an electrical business called "Corvane Electrical and Communications" i need the cards to be double sided with the company logo on the back (attached) the front needs to say my company name, web site, email address, telephone number, and ABN number and electrical license number. I am open to different arrangements of the information but would like the background to be incorporating something electrical or something that looks smart. open to all additional ideas also.

The company colours are orange and grey see logo attached.

Business Name: Corvane Electrical and Communications
Website: corvaneelectricalandcomms.example.com.au
Email: brent@corvaneelectricalandcomms.example.com.au
Telephone(mobile): 0481209736
ABN: 71208349162
Lic No: 418273D

Target Market(s)

Business entities, Project Managers, Accounts, Clients

Industry/Entity Type

Electrician

Contact Information for Business Card

I need a design for business cards, i am an electrical business called "Corvane Electrical and Communications" i need the cards to be double sided with the company logo on the back (attached) the front needs to say my company name

Font styles to use
Serif
Sans Serif

Colors
f37122
5c5c5c

Requirements
Must have
• Must have the Logo on the back open to different ways of it being on the back but had in mind to keep it central but again open to other options
Nice to have
• A real modern cool background that is eye catching yet contemporary
Should not have
• No backgrounds of a light bulb or plug or anything like that

```html
<!DOCTYPE html>
<html lang="en">
<head>
<meta charset="utf-8">
<title>Corvane Electrical and Communications — Business Card</title>
<link rel="stylesheet" href="https://fonts.googleapis.com/css2?family=Exo+2:wght@400;600&display=swap">
<style>
  :root {
    --orange: #f37122;
    --grey: #5c5c5c;
    --stage: #e8e5e1;
    --card-dark: #151515;
    --card-mid: #2e2e2e;
    --text-light: #f2f2f2;
    --text-muted: #cfcfcf;
  }
  * { box-sizing: border-box; margin: 0; padding: 0; }
  html, body {
    width: 1200px;
    height: 969px;
    overflow: hidden;
    background: var(--stage);
  }
  .canvas {
    position: relative;
    width: 1200px;
    height: 969px;
  }
  .card {
    position: absolute;
    left: 355px;
    top: 54px;
    width: 490px;
    height: 860px;
    border-radius: 30px;
    background:
      radial-gradient(ellipse at 35% 25%, rgba(255,255,255,0.10), transparent 60%),
      linear-gradient(160deg, var(--card-mid) 0%, var(--card-dark) 55%, #232323 100%);
    box-shadow: 0 20px 50px rgba(0,0,0,0.25);
    font-family: "Exo 2", sans-serif;
    text-align: center;
    overflow: hidden;
  }
  .card-frame {
    position: absolute;
    inset: 0;
    width: 100%;
    height: 100%;
  }
  .brand-name {
    position: absolute;
    left: 0;
    right: 0;
    top: 130px;
    color: var(--orange);
    font-weight: 600;
    font-size: 30px;
    line-height: 1.3;
    letter-spacing: 1.5px;
    text-transform: uppercase;
  }
  .block {
    position: absolute;
    left: 0;
    right: 0;
  }
  .icon {
    display: block;
    margin: 0 auto;
    width: 26px;
    height: 26px;
  }
  .person-name {
    color: var(--orange);
    font-weight: 600;
    font-size: 30px;
    letter-spacing: 1px;
    text-transform: uppercase;
    margin-top: 6px;
  }
  .person-role {
    color: var(--text-light);
    font-weight: 600;
    font-size: 24px;
    letter-spacing: 1px;
    text-transform: uppercase;
    margin-top: 2px;
  }
  .contact-text {
    color: var(--text-muted);
    font-weight: 400;
    font-size: 21px;
    margin-top: 6px;
  }
  .contact-text.small { font-size: 17px; }
  .registration {
    color: var(--text-muted);
    font-weight: 400;
    font-size: 22px;
    line-height: 1.5;
  }
</style>
</head>
<body>
<main class="canvas">
  <section class="card" aria-label="Business card front">
    <svg class="card-frame" viewBox="0 0 490 860" aria-hidden="true">
      <rect x="14" y="14" width="462" height="832" rx="20" fill="none" stroke="var(--orange)" stroke-width="3"/>
    </svg>

    <h1 class="brand-name">Corvane<br>Electrical &amp; Communications</h1>

    <div class="block" style="top:270px">
      <svg class="icon" viewBox="0 0 24 24" aria-hidden="true">
        <circle cx="12" cy="8" r="5" fill="var(--orange)"/>
        <path d="M3 23c0-5 4-8.5 9-8.5s9 3.5 9 8.5z" fill="var(--orange)"/>
      </svg>
      <p class="person-name">Daniel Reyes</p>
      <p class="person-role">CEO/Founder</p>
    </div>

    <div class="block" style="top:404px">
      <svg class="icon" viewBox="0 0 24 24" aria-hidden="true">
        <rect x="6" y="1" width="12" height="22" rx="2" fill="none" stroke="var(--orange)" stroke-width="2"/>
        <line x1="10" y1="19" x2="14" y2="19" stroke="var(--orange)" stroke-width="2"/>
      </svg>
      <p class="contact-text">0481209736</p>
    </div>

    <div class="block" style="top:472px">
      <svg class="icon" viewBox="0 0 24 24" aria-hidden="true">
        <rect x="2" y="5" width="20" height="14" rx="1.5" fill="var(--orange)"/>
        <path d="M2.5 6l9.5 7 9.5-7" fill="none" stroke="var(--card-dark)" stroke-width="1.6"/>
      </svg>
      <p class="contact-text small">brent@corvaneelectricalandcomms.example.com.au</p>
    </div>

    <div class="block" style="top:536px">
      <svg class="icon" viewBox="0 0 24 24" aria-hidden="true">
        <circle cx="12" cy="12" r="10" fill="none" stroke="var(--orange)" stroke-width="2"/>
        <ellipse cx="12" cy="12" rx="4.5" ry="10" fill="none" stroke="var(--orange)" stroke-width="1.6"/>
        <line x1="2" y1="12" x2="22" y2="12" stroke="var(--orange)" stroke-width="1.6"/>
      </svg>
      <p class="contact-text small">corvaneelectricalandcomms.example.com.au</p>
    </div>

    <div class="block registration" style="top:618px">
      <p>ABN: 71208349162</p>
      <p>Lic No: 418273D</p>
    </div>
  </section>
</main>
</body>
</html>
```